Business IT Services Billboard to attract local small businesses

We are Brivoqua, a premier Managed Service Provider (MSP) specializing in comprehensive IT services and VOIP phone solutions exclusively for businesses. Our goal is to create a dynamic and visually engaging billboard advertisement that not only highlights our cutting-edge IT solutions but also emphasizes our state-of-the-art VOIP phone services. This billboard should communicate our commitment to providing innovative, reliable, and holistic technology solutions.
See the attached supporting documentation.
Target Market(s)
small business
Industry/Entity Type
Information Technology
Colors
Designer to choose colors to be used in the design.
Look and feel
Each slider illustrates characteristics of the customer's brand and the style your logo design should communicate.

```html
<!DOCTYPE html>
<html lang="en">
<head>
<meta charset="utf-8">
<title>Brivoqua Billboard</title>
<link rel="stylesheet" href="https://fonts.googleapis.com/css2?family=Bebas+Neue&family=Montserrat:wght@300;600;800&family=Poppins:wght@500&display=swap">
<style>
  :root {
    --brand-blue: #1a6fbb;
    --deep-navy: #0c1a33;
    --signal-orange: #e0500d;
    --soft-grey: #c9c9cb;
    --paper: #ffffff;
    --page: #ffffff;
  }
  html, body {
    margin: 0;
    padding: 0;
    width: 1078px;
    height: 1200px;
    overflow: hidden;
    background: var(--page);
  }
  .canvas {
    position: relative;
    width: 1078px;
    height: 1200px;
  }
  .billboard {
    position: absolute;
    left: 39px;
    top: 466px;
    width: 1000px;
    height: 268px;
    box-shadow: 0 10px 30px rgba(0, 0, 0, 0.22);
    background: var(--paper);
  }
  .billboard svg { display: block; width: 100%; height: 100%; }
  .brand-name { font-family: "Montserrat", sans-serif; font-weight: 800; fill: var(--brand-blue); }
  .headline-main { font-family: "Bebas Neue", sans-serif; fill: var(--brand-blue); }
  .headline-sub { font-family: "Montserrat", sans-serif; font-weight: 300; fill: var(--deep-navy); }
  .headline-focus { font-family: "Montserrat", sans-serif; font-weight: 800; fill: var(--signal-orange); }
  .tagline { font-family: "Poppins", sans-serif; font-weight: 500; fill: var(--deep-navy); }
  .call-to-action { font-family: "Montserrat", sans-serif; font-weight: 800; }
  .cta-dark { fill: var(--deep-navy); }
  .cta-light { fill: var(--paper); }
  .web-address { font-family: "Montserrat", sans-serif; font-weight: 600; fill: var(--paper); }
  .band-navy { fill: var(--deep-navy); }
  .band-blue { fill: var(--brand-blue); }
  .band-orange { fill: var(--signal-orange); }
  .accent-grey { fill: var(--soft-grey); }
</style>
</head>
<body>
<main class="canvas">
  <section class="billboard">
    <svg viewBox="0 0 1507 404" xmlns="http://www.w3.org/2000/svg">
      <defs>
        <linearGradient id="office-tones" x1="0" y1="0" x2="1" y2="1">
          <stop offset="0" stop-color="#4d6f88"/>
          <stop offset="0.45" stop-color="#9fb4c2"/>
          <stop offset="0.75" stop-color="#7d93a8"/>
          <stop offset="1" stop-color="#d7dde2"/>
        </linearGradient>
      </defs>

      <rect class="paper" x="0" y="0" width="1507" height="404" fill="#ffffff"/>

      <polygon class="accent-grey" points="978,0 1013,0 958,96"/>
      <polygon class="accent-grey" points="938,178 1098,334 1062,334 930,196"/>

      <g role="img" aria-label="Photo of smiling support staff wearing headsets at desks in a bright modern office">
        <polygon points="1018,0 1507,0 1507,334 1098,334 943,174" fill="url(#office-tones)"/>
      </g>

      <polygon class="band-navy" points="0,174 940,174 1005,266 0,266"/>
      <polygon class="band-blue" points="0,321 795,321 850,404 0,404"/>
      <polygon class="band-navy" points="843,394 860,394 853,404 848,404"/>
      <polygon class="band-orange" points="798,332 1507,332 1507,380 828,380"/>

      <text class="brand-name" x="38" y="112" font-size="30" textLength="166" lengthAdjust="spacingAndGlyphs">Brivoqua</text>

      <text class="headline-main" x="223" y="108" font-size="98" textLength="700" lengthAdjust="spacingAndGlyphs">SEAMLESS TECHNOLOGY</text>
      <text class="headline-sub" x="223" y="158" font-size="52" textLength="660" lengthAdjust="spacing">SOLUTIONS FOR</text>

      <text class="headline-focus" x="38" y="252" font-size="88" textLength="862" lengthAdjust="spacingAndGlyphs">MODERN BUSINESSES</text>

      <text class="tagline" x="38" y="301" font-size="25" textLength="910" lengthAdjust="spacingAndGlyphs">Innovative IT and VOIP Solutions Tailored for Your Business Success.</text>

      <text class="call-to-action" x="38" y="373" font-size="30" textLength="720" lengthAdjust="spacing"><tspan class="cta-dark">TRANSFORM YOUR </tspan><tspan class="cta-light">TECH TODAY</tspan></text>

      <text class="web-address" x="855" y="367" font-size="32" textLength="605" lengthAdjust="spacing">www.brivoqua.com</text>
    </svg>
  </section>
</main>
</body>
</html>
```